Business Card Design

Buy and sell properties
Buy and rehab properties
Buy properties for cash
That is what I do but do need a logo
looking for some type of logo or design on it
Just started business
Back of card should say something like BUY HOUSES CASH
Overview: it is a new company. Basically I buy properties wholesale and fix them up and sell them or sell them to other fix and flippers
Background: company is new so not any background
Market: is basically anyone selling a house or buying a house. Someone that needs to sell house fast. Basically I am a cash home buyer!!!

Updates
Email on card should be:   harborlanerealtyinc@mailnest.com

Industry/Entity Type
House
Contact Information for Business Card
Harbor Lane Realty Inc
PO Box 718296
Coral Mill Key FL 33071

Dwight Kallum
dkallum@mailnest.com
305-271-5589

```html
<!DOCTYPE html>
<html lang="en">
<head>
<meta charset="utf-8">
<title>Harbor Lane Realty Inc — Business Card</title>
<link rel="stylesheet" href="https://fonts.googleapis.com/css2?family=Ubuntu:wght@400;500;700&display=swap">
<style>
  :root {
    --brand-green: #0f9a45;
    --brand-red: #c4102f;
    --card-white: #fbfbfa;
    --backdrop: #e9e9e7;
    --card-shadow: rgba(0, 0, 0, 0.18);
  }
  * { box-sizing: border-box; margin: 0; padding: 0; }
  html, body {
    width: 1200px; height: 1000px; overflow: hidden;
    background: var(--backdrop);
    font-family: "Ubuntu", sans-serif;
  }
  .canvas {
    position: relative; width: 1200px; height: 1000px;
  }
  .card {
    position: absolute; left: 220px;
    width: 760px; height: 434px;
    background: var(--card-white);
    box-shadow: 0 6px 18px var(--card-shadow);
    overflow: hidden;
  }
  .card--front { top: 50px; }
  .card--back { top: 516px; }

  /* Front */
  .front-mark {
    position: absolute; left: 0; right: 0; top: 0; bottom: 0;
    display: flex; align-items: center; justify-content: center; gap: 22px;
  }
  .mark-square {
    width: 64px; height: 64px; border: 8px solid var(--brand-red);
  }
  .brand-name {
    color: var(--brand-red); font-weight: 500;
    text-transform: uppercase; line-height: 1.05;
  }
  .front-mark .brand-name { font-size: 50px; letter-spacing: 1px; }

  /* Back */
  .green-top {
    position: absolute; left: 0; top: 0; width: 470px; height: 62px;
    background: var(--brand-green);
  }
  .name-band {
    position: absolute; left: 0; top: 78px; width: 470px; height: 70px;
    background: var(--brand-green);
  }
  .name-band .holder-name {
    position: absolute; left: 0; right: 0; top: 0; height: 42px;
    background: var(--card-white);
    color: var(--brand-green); font-weight: 700; font-size: 24px;
    display: flex; align-items: center; justify-content: center;
  }
  .stripe {
    position: absolute; left: 0; height: 12px; background: var(--brand-green);
  }
  .stripe--one { top: 182px; width: 450px; }
  .stripe--two { top: 228px; width: 430px; }
  .contact-line {
    position: absolute; left: 70px;
    color: var(--brand-green); font-size: 19px;
  }
  .contact-line--phone { top: 153px; left: 95px; }
  .contact-line--email { top: 199px; }
  .green-bottom {
    position: absolute; left: 0; top: 256px; width: 410px; bottom: 0;
    background: var(--brand-green);
  }
  .address {
    position: absolute; left: 40px; top: 290px;
    color: var(--card-white); opacity: 0.85;
  }
  .address .company { font-size: 21px; margin-bottom: 6px; }
  .address .line { font-size: 16px; line-height: 1.3; }
  .back-mark {
    position: absolute; left: 470px; right: 20px; top: 160px;
    display: flex; align-items: center; justify-content: center; gap: 12px;
  }
  .back-mark .mark-square { width: 34px; height: 34px; border-width: 5px; }
  .back-mark .brand-name { font-size: 24px; }
  .tagline {
    position: absolute; right: 40px; bottom: 30px;
    color: var(--brand-green); font-size: 20px; font-weight: 500;
    letter-spacing: 6px;
  }
</style>
</head>
<body>
<main class="canvas">
  <section class="card card--front" aria-label="Card front">
    <div class="front-mark">
      <div class="mark-square"></div>
      <div class="brand-name">Harbor Lane<br>Realty Inc</div>
    </div>
  </section>

  <section class="card card--back" aria-label="Card back">
    <div class="green-top"></div>
    <div class="name-band"><div class="holder-name">Dwight Kallum</div></div>
    <div class="stripe stripe--one"></div>
    <div class="stripe stripe--two"></div>
    <p class="contact-line contact-line--phone">Phone : 305-271-5589</p>
    <p class="contact-line contact-line--email">Email : dkallum@mailnest.com</p>
    <div class="green-bottom"></div>
    <div class="address">
      <p class="company">Harbor Lane Realty Inc</p>
      <p class="line">PO Box 718296</p>
      <p class="line">Coral Mill Key FL 33071</p>
    </div>
    <div class="back-mark">
      <div class="mark-square"></div>
      <div class="brand-name">Harbor Lane<br>Realty Inc</div>
    </div>
    <p class="tagline">BUY HOUSES CASH</p>
  </section>
</main>
</body>
</html>
```